New Business Card for Web Design/Internet Marketing Company

Looking for a great looking new business card. We are a 10 year old web design, internet marketing and website management company that works mostly with small businesses.

Our new card needs to better match the colors and style of our website, be bold, extremely usable and slightly edgy.

Target Market(s)

Small/Medium businesses that have websites

Industry/Entity Type

Internet

Requirements
Must have
• Front and back design, full color, rounded corners please

Must use the colors/style of our website (JPG provided)

INFO FOR CARDS (as readable as possible please)
Mark Lenner
President/CEO
mark@trelvanmedia.example
Phone: 555-381-7459
Toll Free: 866-381-7459
Address: 4315 W. Calloway Ave. Ste. 140, Redmesa, NV 85792

THINGS I WANT TO PROMOTE (if there is room):
1. Our Website - www.trelvanmedia.example

2. Social Media
Twitter: @trelvanmedia
Facebook: www.friendhub.example/trelvanmedia

3. Our Services
Web Design
Internet Marketing
Website Management

```html
<!DOCTYPE html>
<html lang="en">
<head>
<meta charset="utf-8">
<title>Trelvan Media — Business Card</title>
<link rel="stylesheet" href="https://fonts.googleapis.com/css2?family=Open+Sans:ital,wght@0,400;0,600;0,700;1,400&display=swap">
<style>
  :root {
    --page: #e9e6e2;
    --blue: #2b9bd8;
    --blue-light: #45aee6;
    --blue-dark: #1d7fbd;
    --blue-band: #2186c6;
    --orange: #f0812a;
    --ink: #2f2f2f;
    --white: #ffffff;
  }
  * { box-sizing: border-box; margin: 0; padding: 0; }
  html, body { width: 1200px; height: 944px; overflow: hidden; }
  body {
    background: var(--page);
    font-family: "Open Sans", Arial, sans-serif;
    position: relative;
  }
  .card {
    position: absolute;
    width: 700px;
    height: 400px;
    border-radius: 34px;
    overflow: hidden;
    box-shadow: 0 8px 24px rgba(0,0,0,.18);
  }

  /* Front */
  .card--front { left: 80px; top: 60px; background: var(--blue); }
  .card--front .swoosh { position: absolute; inset: 0; }
  .front-logo {
    position: absolute; left: 0; right: 0; top: 92px;
    text-align: center; color: var(--white);
  }
  .front-logo .wordmark { font-size: 64px; font-weight: 700; letter-spacing: -1px; }
  .front-logo .tagline { font-size: 20px; font-weight: 400; margin-top: 2px; }
  .services-band {
    position: absolute; left: 0; right: 0; top: 262px; height: 52px;
    background: var(--blue-band);
    border-top: 3px solid var(--blue-dark);
    display: flex; align-items: center; justify-content: center;
    color: var(--white); font-size: 21px; font-weight: 600; letter-spacing: .3px;
  }
  .services-band .dot { margin: 0 10px; }
  .front-url {
    position: absolute; left: 0; right: 0; top: 334px;
    text-align: center; color: var(--white); font-size: 20px; font-weight: 600; letter-spacing: .5px;
  }

  /* Back */
  .card--back { left: 420px; top: 490px; background: var(--white); }
  .back-logo { position: absolute; right: 48px; top: 34px; text-align: right; }
  .back-logo .wordmark { font-size: 46px; font-weight: 700; color: var(--blue); letter-spacing: -1px; }
  .back-logo .tagline { font-size: 15px; color: var(--ink); }
  .person { position: absolute; left: 56px; top: 132px; }
  .person .name { font-size: 26px; font-weight: 600; color: var(--ink); }
  .person .title { font-size: 16px; font-style: italic; color: var(--orange); margin-top: 2px; }
  .address {
    position: absolute; left: 56px; top: 208px;
    display: flex; gap: 12px; font-size: 17px; color: var(--ink); line-height: 1.35;
  }
  .contacts {
    position: absolute; left: 360px; top: 172px;
    list-style: none; font-size: 17px; color: var(--ink); line-height: 1.5;
  }
  .contacts li { display: flex; align-items: center; gap: 10px; white-space: nowrap; }
  .contacts svg, .address svg { flex: none; }
  .contacts .accent { color: var(--orange); }
  .back-swoosh { position: absolute; left: 0; bottom: 0; width: 700px; height: 120px; }
</style>
</head>
<body>

<section class="card card--front" aria-label="Card front">
  <svg class="swoosh" viewBox="0 0 700 400" aria-hidden="true">
    <ellipse cx="360" cy="150" rx="330" ry="120" fill="none" stroke="var(--blue-light)" stroke-width="26" opacity=".7"/>
  </svg>
  <div class="front-logo">
    <div class="wordmark">trelvanmedia</div>
    <div class="tagline">Sites that work</div>
  </div>
  <div class="services-band">
    Web Design<span class="dot">•</span>Internet Marketing<span class="dot">•</span>Website Management
  </div>
  <div class="front-url">www.trelvanmedia.example</div>
</section>

<section class="card card--back" aria-label="Card back">
  <div class="back-logo">
    <div class="wordmark">trelvanmedia</div>
    <div class="tagline">Sites that work</div>
  </div>

  <div class="person">
    <div class="name">Mark Lenner</div>
    <div class="title">President/CEO</div>
  </div>

  <div class="address">
    <svg width="18" height="18" viewBox="0 0 18 18" aria-hidden="true"><path d="M9 2 1 9h2.5v7h4v-5h3v5h4V9H17z" fill="var(--blue)"/></svg>
    <div>4315 W. Calloway Ave.<br>Ste. 140<br>Redmesa, NV 85792</div>
  </div>

  <ul class="contacts">
    <li><svg width="18" height="14" viewBox="0 0 18 14" aria-hidden="true"><rect x="1" y="1" width="16" height="12" rx="2" fill="var(--blue)"/><path d="M1 2l8 6 8-6" stroke="#fff" stroke-width="1.5" fill="none"/></svg><span>mark@trelvanmedia.example</span></li>
    <li><svg width="18" height="18" viewBox="0 0 18 18" aria-hidden="true"><path d="M5 2l3 3-2 2a9 9 0 0 0 5 5l2-2 3 3-2 3C7 16 2 11 2 4z" fill="var(--blue)"/></svg><span>555-381-7459</span></li>
    <li><svg width="18" height="18" viewBox="0 0 18 18" aria-hidden="true"><path d="M5 2l3 3-2 2a9 9 0 0 0 5 5l2-2 3 3-2 3C7 16 2 11 2 4z" fill="var(--blue)"/></svg><span>866-381-7459 (toll free)</span></li>
    <li><svg width="18" height="18" viewBox="0 0 18 18" aria-hidden="true"><circle cx="9" cy="9" r="7" fill="var(--blue)"/></svg><span>@trelvanmedia</span></li>
    <li><svg width="18" height="18" viewBox="0 0 18 18" aria-hidden="true"><rect x="2" y="2" width="14" height="14" rx="2" fill="var(--blue-dark)"/></svg><span>www.<span class="accent">friendhub.example</span>/trelvanmedia</span></li>
  </ul>

  <svg class="back-swoosh" viewBox="0 0 700 120" preserveAspectRatio="none" aria-hidden="true">
    <path d="M0 30 C180 60 380 40 700 70 L700 120 L0 120Z" fill="var(--orange)"/>
    <path d="M0 80 C200 60 420 70 700 60 L700 120 L0 120Z" fill="var(--blue-dark)"/>
    <path d="M0 95 C240 78 460 88 700 82 L700 120 L0 120Z" fill="var(--blue)"/>
  </svg>
</section>

</body>
</html>
```